Web portal for events

The project is about creating a web application - portal for culture events in Denmark.

Design

We aim for very simplistic, light and fully responsive design. The white background is preferable, as well as light color tones. As inspirational points we like the colors used in www.parvolio.com and www.brindlemoor.org

FORMAT AND REQUIREMENTS:
1. Design should be provided based on the wireframes specified as a link below.
2. The design (and all of its pages) should be provided in three resolution variants:
- Desktop
- Tablet
- Phone
3. The design should be provided as PSD, where each page/section should be in its own PSD file
4. All graphical elements in the design should be delivered as single layers which can then be extracted from the PSD.
5. All graphical elements (icons, graphical buttons, etc.) should be provided as vector objects in the PSD, so that they can be exported into different sizes without loss of quality (for responsiveness)
6. The design should use either web safe fonts or Google Fonts.

RESPONSIVENESS
The web application should be visible on any devices (i.e. responsive design)

WIREFRAMES:
https://velkotrams.examplewire.com/projects/fennoplex/prototype/Homepage?key=3b7c19d0f2a84e6c5d1e9a07b4f2c8d6e1a3f590

We expect design of the following wireframes:

Homepage:
https://velkotrams.examplewire.com/projects/fennoplex/Homepage

For arrangører - billede uploaded:
https://velkotrams.examplewire.com/projects/fennoplex/For%20arrang%C3%B8rer%20-%20billede%20uploaded

Further specifications of the project (i.e. functionality, etc.):
https://files.quorvane.net/document/d/8pKw_Rt2mZqLx4NvB7yHc0aEs9uGdJf3TiOb6nVlW1k/edit?usp=sharing

```html
<!DOCTYPE html>
<html lang="da">
<head>
<meta charset="utf-8">
<title>Kulturvej – Din guide til kultur og events</title>
<link href="https://fonts.googleapis.com/css2?family=Open+Sans:wght@400;600;700&display=swap" rel="stylesheet">
<style>
:root{
  --red:#f0441f;
  --red-dark:#b3260f;
  --band:#ebe8e5;
  --ink:#2b2b2b;
  --muted:#666;
  --dark:#3c3c3c;
  --footer:#3d3d3d;
  --line:#e3e0dd;
  --white:#fff;
}
*{box-sizing:border-box;margin:0;padding:0}
html,body{width:807px;height:1200px;overflow:hidden}
body{position:relative;background:var(--white);font-family:'Open Sans',Arial,sans-serif;color:var(--ink)}
.abs{position:absolute}

.site-header{left:0;top:0;width:807px;height:66px;background:var(--red)}
.brand{left:121px;top:10px;color:var(--white);font-weight:700;font-size:24px;letter-spacing:.5px;line-height:1}
.tagline{left:121px;top:41px;color:var(--white);font-size:7.5px}
.account{top:9px;color:var(--white);font-size:8px;font-weight:600}
.search{left:385px;top:30px;width:218px;height:28px;background:var(--white);font-size:8.5px;color:#999;padding:9px 8px}
.search svg{position:absolute;right:8px;top:10px}
.adv-search{left:614px;top:39px;color:var(--white);font-size:8.5px}

.main-nav{left:0;top:66px;width:807px;height:40px;background:var(--band)}
.nav-item{top:0;height:40px;line-height:40px;font-size:8.5px;font-weight:600;color:var(--ink);transform:translateX(-50%)}
.nav-active{left:121px;top:0;width:48px;height:40px;background:var(--red-dark)}
.nav-item.is-active{color:var(--white)}

.hero{left:122px;top:122px;width:564px;height:271px;border:1.5px solid var(--red);background:var(--red)}
.hero-media{left:0;top:0;width:561px;height:219px;background:radial-gradient(ellipse at 50% 10%,#f7dcb2 0%,#d99a5c 35%,#6b3a1e 70%,#1e120b 100%)}
.hero-caption{left:13px;top:227px;width:420px;color:var(--white);font-size:11px;font-weight:600;line-height:17px}
.hero-arrows{left:506px;top:237px}

.section-title{left:122px;top:425px;font-size:12px;font-weight:600}
.sorter{top:427px;font-size:8.5px;color:var(--muted)}
.sorter.label{color:var(--red);font-weight:600}
.area-select{left:437px;top:420px;width:57px;height:22px;border:1px solid #ddd;font-size:8.5px;color:var(--muted);padding:5px 10px}

.card{width:106px;height:140px;border:1px solid var(--line);background:var(--white)}
.card-media{left:-1px;top:-1px;width:106px;height:69px}
.card-title{left:6px;top:75px;font-size:8.5px;font-weight:600;color:var(--ink);white-space:nowrap}
.card-text{left:6px;top:89px;font-size:6.5px;line-height:10.5px;color:var(--muted);white-space:nowrap}
.btn-event,.btn-fav{top:117px;height:22px;line-height:22px;color:var(--white);font-size:6.5px;text-align:center}
.btn-event{left:-1px;width:51px;background:var(--red)}
.btn-fav{left:50px;width:55px;background:var(--dark)}

.pager{top:1109px;font-size:9.5px;font-weight:700;color:var(--ink);transform:translateX(-50%)}
.pager.is-current{color:var(--red)}
.pager.arrow{font-weight:400;color:var(--muted)}

.favorites{left:507px;top:411px;width:179px;height:330px;border:1px solid var(--line)}
.favorites-head{left:0;top:0;width:177px;height:38px;background:var(--band);color:var(--red);font-size:10.5px;font-weight:600;padding:11px 15px}
.fav-item{left:11px;width:156px;height:69px;border-bottom:1px solid var(--line)}
.fav-thumb{left:0;top:0;width:49px;height:44px}
.fav-title{left:59px;top:0;width:100px;font-size:9.5px;line-height:10.5px;color:var(--ink)}
.fav-text{left:59px;width:100px;font-size:7px;line-height:10px;color:var(--muted)}

.newsletter{left:507px;top:762px;width:179px;height:195px;background:var(--dark)}
.newsletter-head{left:0;top:0;width:179px;height:37px;background:var(--red);color:var(--white);font-size:10px;font-weight:600;padding:12px 16px}
.newsletter-text{left:12px;top:46px;width:160px;font-size:7px;line-height:13px;color:#e4e4e4}
.email{left:14px;top:108px;width:150px;height:26px;background:#e6e6e6;font-size:7px;color:#666;padding:9px 10px}
.submit{left:82px;top:149px;width:82px;height:27px;background:var(--red);color:var(--white);font-size:8px;font-weight:600;text-align:center;line-height:27px}

.site-footer{left:0;top:1141px;width:807px;height:59px;background:var(--footer)}
.copyright{left:122px;top:15px;color:#eee;font-size:7.5px}
.footer-links{left:122px;top:32px;color:#eee;font-size:7.5px}
.social{top:20px;width:20px;height:20px}
</style>
</head>
<body>

<header class="site-header abs">
  <div class="brand abs">Kulturvej</div>
  <div class="tagline abs">Din guide til kultur og events</div>
  <div class="account abs" style="left:610px">LOGIN</div>
  <div class="account abs" style="left:656px">SIGNUP</div>
  <div class="search abs">Search
    <svg width="8" height="8" viewBox="0 0 8 8"><circle cx="3.3" cy="3.3" r="2.5" fill="none" stroke="#999" stroke-width="1"/><line x1="5.2" y1="5.2" x2="7.5" y2="7.5" stroke="#999" stroke-width="1"/></svg>
  </div>
  <div class="adv-search abs">Advancved Search</div>
</header>

<nav class="main-nav abs">
  <div class="nav-active abs"></div>
  <div class="nav-item is-active abs" style="left:145px">ALLE</div>
  <div class="nav-item abs" style="left:204px">MUSIK</div>
  <div class="nav-item abs" style="left:267px">SPORT</div>
  <div class="nav-item abs" style="left:330px">TEATER</div>
  <div class="nav-item abs" style="left:401px">UDSTILLING</div>
  <div class="nav-item abs" style="left:475px">AELDRE</div>
  <div class="nav-item abs" style="left:537px">BORN</div>
  <div class="nav-item abs" style="left:603px">MOTION</div>
  <div class="nav-item abs" style="left:676px">DIVERSE</div>
</nav>

<section class="hero abs">
  <div class="hero-media abs" role="img" aria-label="Koncertpublikum med løftede hænder i varmt scenelys"></div>
  <p class="hero-caption abs">Lorem ipsum dolor sit amet, consectetuer adipiscing elit, sed diam nonummy nibh</p>
  <svg class="hero-arrows abs" width="38" height="16" viewBox="0 0 38 16">
    <circle cx="8" cy="8" r="7.5" fill="#fff"/>
    <path d="M11.5 8H5M7.8 5L4.8 8l3 3" fill="none" stroke="#f0441f" stroke-width="1.8"/>
    <circle cx="28" cy="8" r="7.5" fill="#fff"/>
    <path d="M24.5 8H31M28.2 5l3 3-3 3" fill="none" stroke="#f0441f" stroke-width="1.8"/>
  </svg>
</section>

<h2 class="section-title abs">Popular Events</h2>
<div class="sorter label abs" style="left:273px">Sorter :</div>
<div class="sorter abs" style="left:306px">Populare</div>
<div class="sorter abs" style="left:365px">Dato</div>
<div class="sorter abs" style="left:409px">Pris</div>
<div class="area-select abs">Omrade
  <svg style="position:absolute;right:6px;top:9px" width="5" height="3" viewBox="0 0 5 3"><path d="M0 0h5L2.5 3z" fill="#777"/></svg>
</div>

<!-- Row 1 -->
<article class="card abs" style="left:122px;top:466px">
  <div class="card-media abs" role="img" aria-label="Scene med lilla lys og lasere" style="background:linear-gradient(160deg,#3a1c6b,#c2459a 55%,#1b0f33)"></div>
  <h3 class="card-title abs">Emil Varnholt koncer</h3>
  <p class="card-text abs">Lorem ipsum dolor sit amet,<br>consectetuer adipiscing...</p>
  <div class="btn-event abs">SE EVENT</div><div class="btn-fav abs">FAVORITTER</div>
</article>
<article class="card abs" style="left:254px;top:466px">
  <div class="card-media abs" role="img" aria-label="Dansere på scene i hvide kostumer" style="background:linear-gradient(160deg,#2a1a18,#8a5a4a 50%,#1a1010)"></div>
  <h3 class="card-title abs">Est usus legentis</h3>
  <p class="card-text abs">Lorem ipsum dolor sit amet,<br>consectetuer adipiscing...</p>
  <div class="btn-event abs">SE EVENT</div><div class="btn-fav abs">FAVORITTER</div>
</article>
<article class="card abs" style="left:387px;top:466px">
  <div class="card-media abs" role="img" aria-label="Balletdanser på mørk blå scene" style="background:linear-gradient(180deg,#151a3d,#2a2f66 60%,#4a4a7a)"></div>
  <h3 class="card-title abs">Typi non habent</h3>
  <p class="card-text abs">Lorem ipsum dolor sit amet,<br>consectetuer adipiscing...</p>
  <div class="btn-event abs">SE EVENT</div><div class="btn-fav abs">FAVORITTER</div>
</article>

<!-- Row 2 -->
<article class="card abs" style="left:122px;top:627px">
  <div class="card-media abs" role="img" aria-label="Optræden på scene i blåt lys" style="background:linear-gradient(160deg,#1c2a7a,#4a5ac0 50%,#c07ab0)"></div>
  <h3 class="card-title abs">Eodem modo typi</h3>
  <p class="card-text abs">Lorem ipsum dolor sit amet,<br>consectetuer adipiscing...</p>
  <div class="btn-event abs">SE EVENT</div><div class="btn-fav abs">FAVORITTER</div>
</article>
<article class="card abs" style="left:254px;top:627px">
  <div class="card-media abs" role="img" aria-label="Festivalpublikum" style="background:linear-gradient(160deg,#3a4aa0,#a05a8a 50%,#d08a5a)"></div>
  <h3 class="card-title abs">Emil Varnholt koncer</h3>
  <p class="card-text abs">Lorem ipsum dolor sit amet,<br>consectetuer adipiscing...</p>
  <div class="btn-event abs">SE EVENT</div><div class="btn-fav abs">FAVORITTER</div>
</article>
<article class="card abs" style="left:387px;top:627px">
  <div class="card-media abs" role="img" aria-label="Stor koncertscene med lysbolde" style="background:linear-gradient(180deg,#2a2a6a,#7a7ac0 45%,#1a1a3a)"></div>
  <h3 class="card-title abs">Ut wisi enim ad minim</h3>
  <p class="card-text abs">Lorem ipsum dolor sit amet,<br>consectetuer adipiscing...</p>
  <div class="btn-event abs">SE EVENT</div><div class="btn-fav abs">FAVORITTER</div>
</article>

<!-- Row 3 -->
<article class="card abs" style="left:122px;top:789px">
  <div class="card-media abs" role="img" aria-label="Musiker ved keyboard i rødt lys" style="background:radial-gradient(circle at 40% 40%,#f06a2a,#b8160f 55%,#3a0505)"></div>
  <h3 class="card-title abs">Nam liber tempor cum</h3>
  <p class="card-text abs">Lorem ipsum dolor sit amet,<br>consectetuer adipiscing...</p>
  <div class="btn-event abs">SE EVENT</div><div class="btn-fav abs">FAVORITTER</div>
</article>
<article class="card abs" style="left:254px;top:789px">
  <div class="card-media abs" role="img" aria-label="Dansere mod orange himmel" style="background:linear-gradient(180deg,#e8a020,#c06a10 60%,#3a2a10)"></div>
  <h3 class="card-title abs">Ut wisi enim ad minim</h3>
  <p class="card-text abs">Lorem ipsum dolor sit amet,<br>consectetuer adipiscing...</p>
  <div class="btn-event abs">SE EVENT</div><div class="btn-fav abs">FAVORITTER</div>
</article>
<article class="card abs" style="left:387px;top:789px">
  <div class="card-media abs" role="img" aria-label="Dansegruppe i lilla kostumer" style="background:linear-gradient(180deg,#1a1030,#6a3a8a 55%,#c060b0)"></div>
  <h3 class="card-title abs">Eodem modo typi</h3>
  <p class="card-text abs">Lorem ipsum dolor sit amet,<br>consectetuer adipiscing...</p>
  <div class="btn-event abs">SE EVENT</div><div class="btn-fav abs">FAVORITTER</div>
</article>

<!-- Row 4 -->
<article class="card abs" style="left:122px;top:950px">
  <div class="card-media abs" role="img" aria-label="Arenascene med lysbolde" style="background:linear-gradient(180deg,#3a5aa0,#a0c8e0 45%,#2a8a7a 70%,#1a2a4a)"></div>
  <h3 class="card-title abs">Ut wisi enim ad minim</h3>
  <p class="card-text abs">Lorem ipsum dolor sit amet,<br>consectetuer adipiscing...</p>
  <div class="btn-event abs">SE EVENT</div><div class="btn-fav abs">FAVORITTER</div>
</article>
<article class="card abs" style="left:254px;top:950px">
  <div class="card-media abs" role="img" aria-label="Sanger på scene i pink lys" style="background:linear-gradient(160deg,#3a0a2a,#c0207a 50%,#2a0a1a)"></div>
  <h3 class="card-title abs">Nam liber tempor cum</h3>
  <p class="card-text abs">Lorem ipsum dolor sit amet,<br>consectetuer adipiscing...</p>
  <div class="btn-event abs">SE EVENT</div><div class="btn-fav abs">FAVORITTER</div>
</article>
<article class="card abs" style="left:387px;top:950px">
  <div class="card-media abs" role="img" aria-label="DJ-pult med publikum" style="background:linear-gradient(160deg,#6a5a4a,#b8a898 50%,#4a3a2a)"></div>
  <h3 class="card-title abs">Emil Varnholt koncer</h3>
  <p class="card-text abs">Lorem ipsum dolor sit amet,<br>consectetuer adipiscing...</p>
  <div class="btn-event abs">SE EVENT</div><div class="btn-fav abs">FAVORITTER</div>
</article>

<nav aria-label="Sider">
  <span class="pager arrow abs" style="left:295px">«</span>
  <span class="pager abs" style="left:308px">1</span>
  <span class="pager abs" style="left:330px">2</span>
  <span class="pager abs" style="left:351px">3</span>
  <span class="pager abs" style="left:373px">4</span>
  <span class="pager abs" style="left:394px">5</span>
  <span class="pager abs" style="left:416px">6</span>
  <span class="pager is-current abs" style="left:437px">7</span>
  <span class="pager abs" style="left:459px">8</span>
  <span class="pager abs" style="left:480px">9</span>
  <span class="pager arrow abs" style="left:495px">»</span>
</nav>

<aside class="favorites abs">
  <h3 class="favorites-head abs">Mine Favoritter</h3>
  <div class="fav-item abs" style="top:53px">
    <div class="fav-thumb abs" role="img" aria-label="Arenascene med lysbolde" style="background:linear-gradient(180deg,#3a5aa0,#a0c8e0 50%,#2a3a6a)"></div>
    <div class="fav-title abs">Duis autem vel eum iriure dolor in</div>
    <div class="fav-text abs" style="top:22px">Aenean commodo ligula eget dolor.</div>
  </div>
  <div class="fav-item abs" style="top:122px">
    <div class="fav-thumb abs" role="img" aria-label="Balletdanser på blå scene" style="background:linear-gradient(180deg,#151a3d,#2a2f66 60%,#4a4a7a)"></div>
    <div class="fav-title abs">Typi non habent clarita-tem insitam</div>
    <div class="fav-text abs" style="top:22px">Aenean commodo ligula eget dolor.</div>
  </div>
  <div class="fav-item abs" style="top:191px">
    <div class="fav-thumb abs" role="img" aria-label="Dansere på scene" style="background:linear-gradient(160deg,#2a1a18,#8a5a4a 50%,#1a1010)"></div>
    <div class="fav-title abs">Lorem ipsum dolor sit amet</div>
    <div class="fav-text abs" style="top:22px">Aenean commodo ligula eget dolor.</div>
  </div>
  <div class="fav-item abs" style="top:260px">
    <div class="fav-thumb abs" role="img" aria-label="Scene med lilla lys" style="background:linear-gradient(160deg,#3a1c6b,#c2459a 55%,#1b0f33)"></div>
    <div class="fav-title abs">Lorem ipsum dolor sit amet</div>
    <div class="fav-text abs" style="top:22px">Aenean commodo ligula eget dolor.</div>
  </div>
</aside>

<section class="newsletter abs">
  <h3 class="newsletter-head abs">NYHEDSBREV</h3>
  <p class="newsletter-text abs">Duis autem vel eum iriure dolor in hendrerit in vulputate velit esse molestie consequat, vel illum dolore eu feugiat nulla facilisis at vero eros et accumsan .</p>
  <div class="email abs">Email Address</div>
  <div class="submit abs">SUBMIT</div>
</section>

<footer class="site-footer abs">
  <div class="copyright abs">Copyright@2014 Kulturvej. All right reserved.</div>
  <div class="footer-links abs">Privacy Policy &nbsp;&nbsp;|&nbsp;&nbsp; Sitemap</div>
  <span class="social abs" style="left:542px;background:#3b5998"></span>
  <span class="social abs" style="left:567px;background:#2fa6dd"></span>
  <span class="social abs" style="left:592px;background:#c4302b"></span>
  <span class="social abs" style="left:617px;background:#0e76a8"></span>
  <span class="social abs" style="left:642px;background:#cb2027"></span>
  <span class="social abs" style="left:667px;background:#f26522"></span>
</footer>

</body>
</html>
```